Employee Benefits Flyer for Recruiting

We are a Steel Product Supplier and Manufacturer in Toledo Ohio.

We would like to create an "attention getting", one-page handout to give prospective employees (both production and administrative) that illustrates all the benefits we offer as a company. An editable document would be preferable as we add more or change existing benefits in the future. Current benefits include:

Individual and Family Medical Insurance
Dental Insurance
Vision Insurance
Short Term Disability Insurance
Critical Illness and Accident Insurance
No Cost Life Insurance Policy
Education Cost Reimbursement
401K with Company Match
Profit Sharing
Attendance and Performance Bonuses
No Cost Legal Assistance
No Cost Counseling Services
No Cost Tobacco Cessation Coaching
No Cost College Planning Assistance
No Cost Work-Life Services
No Cost Employee Discounts
No Cost Legal Consultation
No Cost Financial Consultation
No Cost ID Theft Assistance
No Cost Tax Consultation Assistance
Up to 17 Days of Paid Time Off

Target Market(s)

Potential Employees

Industry/Entity Type

Industrial Manufacturing

Requirements
Must have
• Nicely laid out illustrations / engaging content

```html
<!DOCTYPE html>
<html lang="en">
<head>
<meta charset="utf-8">
<title>Keystone Metal Works – Employee Benefits</title>
<link href="https://fonts.googleapis.com/css2?family=Oswald:wght@400;500;600&family=Montserrat:wght@800;900&display=swap" rel="stylesheet">
<style>
  :root {
    --page-bg: #e4e5e7;
    --paper: #ffffff;
    --slate: #3e4a5c;
    --royal: #1f4fcc;
    --navy: #0b2a8c;
    --ink: #1b1f27;
    --roof-blue: #2f7fb8;
    --roof-gray: #a9b2ba;
  }
  * { margin: 0; padding: 0; box-sizing: border-box; }
  html, body { width: 1003px; height: 1200px; overflow: hidden; background: var(--page-bg); }
  .flyer {
    position: absolute; left: 76px; top: 0;
    width: 850px; height: 1200px;
    background: var(--paper); overflow: hidden;
  }
  .edge-photo {
    position: absolute; left: 0; top: 0; width: 36px; height: 1200px;
    background: linear-gradient(180deg, #7a8a96 0%, #3f79b0 30%, #9aa7b0 55%, #6b5a52 80%, #ffffff 100%);
  }
  .edge-band { position: absolute; left: 0; top: 0; width: 36px; height: 1200px; }
  .benefits-column {
    position: absolute; left: 36px; top: 0; width: 390px; height: 1200px;
    background: var(--paper); box-shadow: 3px 0 8px rgba(0,0,0,.12);
  }
  .section-title {
    position: absolute; left: 36px; top: 36px; width: 409px; height: 54px;
    background: var(--slate); color: #fff;
    font: 500 39px/54px "Oswald", sans-serif; letter-spacing: .5px;
    padding-left: 26px; z-index: 3;
  }
  .benefit-grid {
    position: absolute; left: 43px; top: 132px;
    display: grid; grid-template-columns: repeat(3, 125px); grid-auto-rows: 139px;
  }
  .benefit { display: flex; flex-direction: column; align-items: center; text-align: center; }
  .benefit svg { width: 85px; height: 85px; display: block; }
  .benefit p {
    margin-top: 9px; font: 500 12.5px/14px "Oswald", sans-serif; color: var(--ink); white-space: nowrap;
  }
  .site-photo { position: absolute; left: 426px; top: 0; width: 424px; height: 700px; }
  .brand {
    position: absolute; left: 426px; top: 900px; width: 424px; text-align: center;
  }
  .brand-mark { width: 64px; height: 64px; border-radius: 50%; background: var(--royal); margin: 0 auto 18px; }
  .brand-name { font: 900 27px/1 "Montserrat", sans-serif; color: var(--royal); letter-spacing: .3px; }
  .contact {
    position: absolute; left: 443px; top: 1056px; width: 407px; height: 107px;
    background: var(--slate); border-radius: 24px 0 0 24px;
    box-shadow: 0 8px 14px rgba(0,0,0,.25);
    color: #fff; text-align: center; padding-top: 12px;
  }
  .contact-phone { font: 900 44px/1 "Montserrat", sans-serif; letter-spacing: 1px; }
  .contact-web { font: 800 27px/1 "Montserrat", sans-serif; margin-top: 6px; }
</style>
</head>
<body>
<main class="flyer">
  <div class="edge-photo" role="img" aria-label="Aerial photo of the steel plant building"></div>
  <svg class="edge-band" viewBox="0 0 36 1200" aria-hidden="true">
    <path d="M0 1075 L36 1040 L36 1080 L0 1122 Z" fill="var(--royal)"/>
  </svg>

  <svg class="site-photo" viewBox="0 0 424 700" role="img" aria-label="Aerial photo of the blue steel plant roofs and yard">
    <defs>
      <linearGradient id="roofs" x1="0" y1="0" x2="1" y2="1">
        <stop offset="0" stop-color="#b9b3a6"/>
        <stop offset=".25" stop-color="#a7b0b8"/>
        <stop offset=".5" stop-color="var(--roof-blue)"/>
        <stop offset=".8" stop-color="#1f5f8e"/>
        <stop offset="1" stop-color="#3b8ac4"/>
      </linearGradient>
    </defs>
    <path d="M0 0 H424 V688 Q210 640 0 672 Z" fill="url(#roofs)"/>
    <path d="M0 672 Q210 640 424 688 L424 700 Q210 652 0 684 Z" fill="#fff"/>
    <path d="M0 672 Q210 640 424 688 L424 678 Q210 628 0 660 Z" fill="var(--royal)"/>
  </svg>

  <div class="benefits-column"></div>
  <h1 class="section-title">WE OFFER THE BENEFITS</h1>

  <svg width="0" height="0" style="position:absolute">
    <defs>
      <linearGradient id="disc" x1="0" y1="0" x2="1" y2="1">
        <stop offset="0" stop-color="var(--royal)"/>
        <stop offset="1" stop-color="var(--navy)"/>
      </linearGradient>
      <symbol id="ring" viewBox="0 0 100 100"><circle cx="50" cy="50" r="50" fill="url(#disc)"/></symbol>
    </defs>
  </svg>

  <section class="benefit-grid">
    <div class="benefit"><svg viewBox="0 0 100 100"><use href="#ring"/><path d="M44 28h12v16h16v12H56v16H44V56H28V44h16z" fill="#fff"/></svg><p>Short Term<br>Disability Insurance</p></div>
    <div class="benefit"><svg viewBox="0 0 100 100"><use href="#ring"/><path d="M50 24l22 8v16c0 14-10 24-22 28-12-4-22-14-22-28V32z" fill="#fff"/><path d="M40 50l7 7 14-14" stroke="var(--navy)" stroke-width="5" fill="none"/></svg><p>Critical Illness &amp;<br>Accident Insurance</p></div>
    <div class="benefit"><svg viewBox="0 0 100 100"><use href="#ring"/><path d="M50 24l22 8v16c0 14-10 24-22 28-12-4-22-14-22-28V32z" fill="none" stroke="#fff" stroke-width="5"/><circle cx="50" cy="46" r="7" fill="#fff"/></svg><p>No Cost Life<br>Insurance Policy</p></div>

    <div class="benefit"><svg viewBox="0 0 100 100"><use href="#ring"/><path d="M30 52l13 13 27-28" stroke="#fff" stroke-width="8" fill="none" stroke-linecap="round"/></svg><p>Attendance and<br>Performance Bonuses</p></div>
    <div class="benefit"><svg viewBox="0 0 100 100"><use href="#ring"/><rect x="40" y="24" width="26" height="14" rx="2" transform="rotate(40 53 31)" fill="#fff"/><rect x="30" y="44" width="7" height="26" transform="rotate(-50 33 57)" fill="#fff"/><rect x="28" y="68" width="32" height="7" rx="2" fill="#fff"/></svg><p>No Cost<br>Legal Assistance</p></div>
    <div class="benefit"><svg viewBox="0 0 100 100"><use href="#ring"/><path d="M28 30h44v28H48l-12 10v-10h-8z" fill="#fff"/></svg><p>No Cost<br>Counseling Services</p></div>

    <div class="benefit"><svg viewBox="0 0 100 100"><use href="#ring"/><text x="50" y="64" text-anchor="middle" font-family="Montserrat,sans-serif" font-weight="900" font-size="40" fill="#fff">%</text></svg><p>No Cost Employee<br>Discounts</p></div>
    <div class="benefit"><svg viewBox="0 0 100 100"><use href="#ring"/><path d="M26 28h36v22H42l-10 9v-9h-6z" fill="#fff"/><path d="M48 54h26v20h-5v8l-9-8H48z" fill="#fff" opacity=".8"/></svg><p>No Cost Legal<br>Consultation</p></div>
    <div class="benefit"><svg viewBox="0 0 100 100"><use href="#ring"/><text x="50" y="66" text-anchor="middle" font-family="Montserrat,sans-serif" font-weight="900" font-size="44" fill="#fff">$</text></svg><p>No Cost Financial<br>Consultation</p></div>

    <div class="benefit"><svg viewBox="0 0 100 100"><use href="#ring"/><path d="M44 26h12v18h18v12H56v18H44V56H26V44h18z" fill="#fff"/></svg><p>Individual &amp; Family<br>Medical Insurance</p></div>
    <div class="benefit"><svg viewBox="0 0 100 100"><use href="#ring"/><path d="M50 24l22 8v16c0 14-10 24-22 28-12-4-22-14-22-28V32z" fill="#fff"/><path d="M40 50l7 7 14-14" stroke="var(--navy)" stroke-width="5" fill="none"/></svg><p>Dental<br>Insurance</p></div>
    <div class="benefit"><svg viewBox="0 0 100 100"><use href="#ring"/><path d="M20 50q30-28 60 0q-30 28-60 0z" fill="#fff"/><circle cx="50" cy="50" r="10" fill="var(--navy)"/></svg><p>Vision<br>Insurance</p></div>

    <div class="benefit"><svg viewBox="0 0 100 100"><use href="#ring"/><path d="M50 28l28 12-28 12-28-12z" fill="#fff"/><path d="M34 46v12c8 6 24 6 32 0V46l-16 7z" fill="#fff"/></svg><p>Education Cost<br>Reimbursement</p></div>
    <div class="benefit"><svg viewBox="0 0 100 100"><use href="#ring"/><rect x="30" y="28" width="40" height="44" rx="6" fill="#fff"/><text x="50" y="62" text-anchor="middle" font-family="Montserrat,sans-serif" font-weight="900" font-size="30" fill="var(--navy)">$</text></svg><p>401K with<br>Company Match</p></div>
    <div class="benefit"><svg viewBox="0 0 100 100"><use href="#ring"/><path d="M48 30a22 22 0 1 0 22 22H48z" fill="#fff"/><path d="M54 24v22h22a22 22 0 0 0-22-22z" fill="#fff"/></svg><p>Profit<br>Sharing</p></div>

    <div class="benefit"><svg viewBox="0 0 100 100"><use href="#ring"/><rect x="22" y="54" width="46" height="11" fill="#fff"/><rect x="70" y="54" width="8" height="11" fill="#fff"/><path d="M66 26q-6 8 0 14t0 12M74 26q-6 8 0 14t0 12" stroke="#fff" stroke-width="3" fill="none"/></svg><p>No Cost Tobacco<br>Cessation Coaching</p></div>
    <div class="benefit"><svg viewBox="0 0 100 100"><use href="#ring"/><path d="M50 28l30 13-30 13-30-13z" fill="#fff"/><path d="M36 48v14c8 6 20 6 28 0V48l-14 6z" fill="#fff"/><path d="M74 44v18" stroke="#fff" stroke-width="3"/></svg><p>No Cost College<br>Planning Assistance</p></div>
    <div class="benefit"><svg viewBox="0 0 100 100"><use href="#ring"/><rect x="24" y="36" width="52" height="34" rx="4" fill="#fff"/><path d="M40 36v-6h20v6" stroke="#fff" stroke-width="4" fill="none"/><path d="M24 50h52" stroke="var(--navy)" stroke-width="3"/></svg><p>No Cost Work-<br>Life Services</p></div>

    <div class="benefit"><svg viewBox="0 0 100 100"><use href="#ring"/><rect x="24" y="32" width="52" height="36" rx="4" fill="#fff"/><rect x="30" y="40" width="14" height="18" fill="var(--navy)"/><path d="M50 42h20M50 50h20M50 58h14" stroke="var(--navy)" stroke-width="3"/></svg><p>No Cost ID<br>Theft Assistance</p></div>
    <div class="benefit"><svg viewBox="0 0 100 100"><use href="#ring"/><path d="M32 24h26l10 10v42H32z" fill="#fff"/><path d="M38 40h22M38 48h22M38 56h14" stroke="var(--navy)" stroke-width="3"/><circle cx="62" cy="64" r="8" fill="none" stroke="#fff" stroke-width="4"/></svg><p>No Cost Tax<br>Consultation Assistance</p></div>
    <div class="benefit"><svg viewBox="0 0 100 100"><use href="#ring"/><path d="M34 42a22 18 0 0 1 44 0z" fill="#fff"/><path d="M56 42v26" stroke="#fff" stroke-width="3"/><path d="M22 70h56" stroke="#fff" stroke-width="5" stroke-linecap="round"/></svg><p>Up to 17 Days<br>of Paid Time Off</p></div>
  </section>

  <div class="brand">
    <div class="brand-mark"></div>
    <div class="brand-name">KEYSTONE METAL WORKS</div>
  </div>

  <div class="contact">
    <div class="contact-phone">555-204-7731</div>
    <div class="contact-web">KEYSTONEMETAL.COM</div>
  </div>
</main>
</body>
</html>
```